Volbrey Inc Business Card

Looking to get an updated business card for a Contract Machining company (www.volbreyinc.example) - looking for a clean design the portrays the technical nature of the business - colors can follow the website design and be in any combination that makes sense (red black, white, metallic or silver) - logos attached for use also. Would like space for: Name, title, business phone (555 214-3086), cell phone , website (www.volbreyinc.example) - possibly QR code could be integrated for website (designer choice), business address - 418 Harlow Bend, Corrin Falls, NX 48199 (cards will be for 4 employees, I will either need to modify a template or I can provide individual information)
Target Market(s)
Aerospace, defense and medical device manufacturing companies that need machining
Industry/Entity Type
Machining for aerospace, defense, medical
Contact Information for Business Card
Name, Title, Business Phone, Cell Phone, email, business website and business address
Look and feel

```html
<!DOCTYPE html>
<html lang="en">
<head>
<meta charset="utf-8">
<title>Volbrey Inc Business Card</title>
<link rel="stylesheet" href="https://fonts.googleapis.com/css2?family=Montserrat:wght@400;500;700;800&display=swap">
<style>
  :root {
    --backdrop: #3b3b3d;
    --brand-red: #b11e25;
    --paper: #ffffff;
    --arc-grey: #7a7a7a;
    --text-light: #ffffff;
  }
  * { box-sizing: border-box; margin: 0; padding: 0; }
  html, body { width: 1200px; height: 689px; overflow: hidden; }
  body {
    background: var(--backdrop);
    font-family: "Montserrat", Arial, sans-serif;
    position: relative;
  }
  .card {
    position: absolute;
    width: 525px;
    height: 300px;
    border-radius: 22px;
    overflow: hidden;
    box-shadow: 0 14px 30px rgba(0,0,0,.45);
  }
  .card-back { left: 50px; top: 195px; background: var(--brand-red); }
  .card-front { left: 625px; top: 195px; background: var(--brand-red); }

  /* back side */
  .back-mark {
    position: absolute; left: 50%; top: 118px;
    transform: translate(-50%, -50%);
    display: flex; align-items: center; gap: 14px;
    white-space: nowrap;
  }
  .back-mark .dot {
    width: 34px; height: 34px; border-radius: 50%;
    background: var(--paper); flex: none;
  }
  .back-mark .name {
    color: var(--text-light); font-weight: 800; font-size: 34px; letter-spacing: 1px;
  }
  .back-web {
    position: absolute; left: 0; right: 0; top: 222px;
    text-align: center; color: var(--text-light); font-size: 15px; font-weight: 500;
  }

  /* front side */
  .front-shapes { position: absolute; inset: 0; }
  .front-mark {
    position: absolute; left: 52px; top: 128px;
    display: flex; align-items: center; gap: 12px;
    white-space: nowrap;
  }
  .front-mark .dot {
    width: 30px; height: 30px; border-radius: 50%; background: var(--brand-red); flex: none;
  }
  .front-mark .name {
    color: var(--brand-red); font-weight: 800; font-size: 32px; letter-spacing: 1px;
  }
  .details {
    position: absolute; right: 26px; top: 22px;
    text-align: right; color: var(--text-light);
    white-space: nowrap;
  }
  .details .company { font-weight: 800; font-size: 26px; letter-spacing: 1px; line-height: 1; }
  .details .company-sub { font-size: 11px; font-weight: 500; letter-spacing: 2px; margin-top: 2px; }
  .details .person { font-weight: 700; font-size: 19px; margin-top: 16px; line-height: 1; }
  .details .role { font-size: 11px; margin-top: 3px; }
  .details .address { font-size: 11.5px; line-height: 1.4; margin-top: 16px; }
  .contacts { list-style: none; margin-top: 10px; font-size: 11.5px; line-height: 1.55; }
  .contacts li { display: flex; justify-content: flex-end; align-items: center; gap: 7px; }
  .contacts svg { width: 11px; height: 11px; fill: var(--text-light); flex: none; }
</style>
</head>
<body>

  <section class="card card-back" aria-label="Card back">
    <div class="back-mark">
      <span class="dot"></span>
      <span class="name">VOLBREY INC</span>
    </div>
    <p class="back-web">www.volbreyinc.example</p>
  </section>

  <section class="card card-front" aria-label="Card front">
    <svg class="front-shapes" viewBox="0 0 525 300" width="525" height="300" aria-hidden="true">
      <circle cx="110" cy="155" r="212" fill="var(--arc-grey)"/>
      <circle cx="100" cy="160" r="210" fill="var(--paper)"/>
    </svg>
    <div class="front-mark">
      <span class="dot"></span>
      <span class="name">VOLBREY</span>
    </div>
    <div class="details">
      <p class="company">VOLBREY</p>
      <p class="company-sub">INC.</p>
      <p class="person">Daniel Reyes</p>
      <p class="role">President</p>
      <p class="address">418 Harlow Bend<br>Corrin Falls, NX 48199</p>
      <ul class="contacts">
        <li>555 214-3086
          <svg viewBox="0 0 24 24"><path d="M6.6 10.8a15 15 0 0 0 6.6 6.6l2.2-2.2a1 1 0 0 1 1-.25 11.4 11.4 0 0 0 3.6.57 1 1 0 0 1 1 1V20a1 1 0 0 1-1 1A17 17 0 0 1 3 4a1 1 0 0 1 1-1h3.5a1 1 0 0 1 1 1c0 1.25.2 2.45.57 3.57a1 1 0 0 1-.25 1z"/></svg></li>
        <li>555 308-7142
          <svg viewBox="0 0 24 24"><path d="M7 1h10a2 2 0 0 1 2 2v18a2 2 0 0 1-2 2H7a2 2 0 0 1-2-2V3a2 2 0 0 1 2-2zm0 3v14h10V4zm5 15.5a1 1 0 1 0 0 2 1 1 0 0 0 0-2z"/></svg></li>
        <li>info@volbreyinc.example
          <svg viewBox="0 0 24 24"><path d="M2 5h20v14H2zm2 2v.5l8 5 8-5V7zm0 2.8V17h16V9.8l-8 5z"/></svg></li>
        <li>www.volbreyinc.example
          <svg viewBox="0 0 24 24"><path d="M12 2a10 10 0 1 0 0 20 10 10 0 0 0 0-20zm6.9 9h-3a15 15 0 0 0-1.3-5.6A8 8 0 0 1 18.9 11zM12 4c.9 1.2 1.8 3.6 1.9 7h-3.8c.1-3.4 1-5.8 1.9-7zM9.4 5.4A15 15 0 0 0 8.1 11h-3a8 8 0 0 1 4.3-5.6zM5.1 13h3a15 15 0 0 0 1.3 5.6A8 8 0 0 1 5.1 13zm6.9 7c-.9-1.2-1.8-3.6-1.9-7h3.8c-.1 3.4-1 5.8-1.9 7zm2.6-1.4a15 15 0 0 0 1.3-5.6h3a8 8 0 0 1-4.3 5.6z"/></svg></li>
      </ul>
    </div>
  </section>

</body>
</html>
```